Design a web site for my business - Brightline Coatings Co.

We are a family business that handles design, fabrication and installation of powder coated aluminum, stainless steel and glass products. Including handrails, privacy slat screens, electric gates and pool fencing. We are based in the Whitsundays in North Queensland and service an area from Airlie Beach to Townsville.

Target Market(s)

Domestic and commercial

Industry/Entity Type

fabrication - manufacturing

Coding

Coded - Design and coding required

Number of Pages Required

5+ page

Colors
0054AA
0677BA
7BADD7
CADEEF
E8F1F8

Requirements
Must have
• photo galleries, contact page, one page for privacy screens, balustrades, glass fencing, stainless steel handrail, powder coated aluminium handrails and pool fencing

```html
<!DOCTYPE html>
<html lang="en">
<head>
<meta charset="UTF-8">
<title>Brightline Coatings Co — Precision Fabrication</title>
<link rel="stylesheet" href="https://fonts.googleapis.com/css2?family=Plus+Jakarta+Sans:wght@300;400;500;600;700;800&display=swap">
<style>
  :root {
    --brand-blue: #0054AA;
    --mid-blue: #0677BA;
    --sky-blue: #7BADD7;
    --pale-blue: #CADEEF;
    --mist: #E8F1F8;
    --ink: #1b1f26;
    --muted: #4a5260;
    --white: #ffffff;
  }
  * { box-sizing: border-box; margin: 0; padding: 0; }
  html, body { width: 1200px; height: 900px; overflow: hidden; }
  body {
    font-family: "Plus Jakarta Sans", sans-serif;
    background: var(--mist);
    color: var(--ink);
  }
  .site { width: 1200px; height: 900px; display: flex; flex-direction: column; }

  .site-header {
    height: 90px;
    background: var(--mist);
    display: flex;
    align-items: center;
    justify-content: space-between;
    padding: 0 70px 0 70px;
    flex-shrink: 0;
  }
  .brand { display: flex; align-items: center; gap: 10px; }
  .brand-mark { width: 14px; height: 14px; background: var(--brand-blue); }
  .brand-name { font-size: 15px; font-weight: 700; color: #3a4250; letter-spacing: 0.02em; text-transform: uppercase; }
  .main-nav { display: flex; gap: 34px; height: 90px; align-items: center; }
  .nav-link {
    position: relative;
    font-size: 14px;
    font-weight: 400;
    color: #3a4250;
    text-decoration: none;
    height: 90px;
    display: flex;
    align-items: center;
  }
  .nav-link.is-active { font-weight: 700; color: var(--ink); }
  .nav-link.is-active::after {
    content: "";
    position: absolute;
    left: -8px; right: -8px; bottom: 0;
    height: 3px;
    background: #3a4250;
  }

  .hero {
    position: relative;
    height: 520px;
    flex-shrink: 0;
    overflow: hidden;
  }
  .hero-photo {
    position: absolute; inset: 0;
    background:
      linear-gradient(90deg, rgba(20,26,32,0.55) 0%, rgba(20,26,32,0.15) 60%, rgba(20,26,32,0.1) 100%),
      radial-gradient(ellipse at 55% 45%, #4a3a30 0%, #3a3630 25%, transparent 50%),
      linear-gradient(180deg, #5c6570 0%, #4f5860 40%, #2f3d2c 72%, #3b3a30 100%);
  }
  .hero-content { position: relative; padding: 130px 0 0 92px; color: var(--white); }
  .hero-title {
    font-size: 66px;
    font-weight: 800;
    line-height: 1.12;
    text-transform: uppercase;
    letter-spacing: -0.01em;
  }
  .hero-lead {
    margin-top: 22px;
    font-size: 18px;
    font-weight: 400;
    line-height: 1.5;
    max-width: 620px;
  }
  .hero-actions { display: flex; gap: 16px; margin-top: 34px; }
  .btn {
    display: inline-flex; align-items: center;
    height: 56px; padding: 0 24px;
    border-radius: 28px;
    font-family: inherit;
    font-size: 18px;
    font-weight: 600;
    text-decoration: none;
    color: var(--white);
  }
  .btn-primary { background: var(--brand-blue); }
  .btn-ghost { background: rgba(255,255,255,0.08); border: 1px solid rgba(255,255,255,0.35); }

  .about {
    flex: 1;
    display: grid;
    grid-template-columns: 1fr 1fr;
    gap: 60px;
    padding: 40px 70px 0 92px;
  }
  .about-copy p { font-size: 15px; line-height: 1.65; color: var(--muted); margin-bottom: 14px; max-width: 440px; }
  .about-side { display: flex; gap: 24px; }
  .about-heading-block { flex: 1; }
  .eyebrow { display: flex; align-items: center; gap: 10px; color: var(--brand-blue); font-size: 12px; font-weight: 600; }
  .eyebrow::before { content: ""; width: 40px; height: 1px; background: var(--brand-blue); }
  .about-title { margin-top: 12px; font-size: 26px; font-weight: 800; line-height: 1.15; text-transform: uppercase; }
  .about-photo {
    position: relative;
    width: 200px; height: 210px;
    background: linear-gradient(160deg, #8fb3cf 0%, #5d7f6a 55%, #7a5a3c 100%);
  }
  .stat-badge {
    position: absolute; left: -22px; bottom: 18px;
    background: var(--white);
    padding: 10px 14px;
    box-shadow: 0 6px 18px rgba(0,40,90,0.12);
  }
  .stat-value { font-size: 22px; font-weight: 800; color: var(--brand-blue); }
  .stat-label { font-size: 10px; color: var(--muted); }
</style>
</head>
<body>
<div class="site">
  <header class="site-header">
    <div class="brand">
      <span class="brand-mark"></span>
      <span class="brand-name">Brightline Coatings Co</span>
    </div>
    <nav class="main-nav">
      <a class="nav-link is-active" href="#">Home</a>
      <a class="nav-link" href="#">About Us</a>
      <a class="nav-link" href="#">Our Services</a>
      <a class="nav-link" href="#">Gallery</a>
      <a class="nav-link" href="#">Contact Us</a>
    </nav>
  </header>

  <section class="hero">
    <div class="hero-photo" role="img" aria-label="Elevated timber house with glass balustrade deck surrounded by tropical garden under an overcast sky"></div>
    <div class="hero-content">
      <h1 class="hero-title">Precision Fabrication<br>Built to Last</h1>
      <p class="hero-lead">Custom aluminium and stainless steel handrails, glass balustrades and gates — designed, fabricated and installed by a family-owned Whitsundays team.</p>
      <div class="hero-actions">
        <a class="btn btn-primary" href="#">Request Free Quote</a>
        <a class="btn btn-ghost" href="#">View Projects</a>
      </div>
    </div>
  </section>

  <section class="about">
    <div class="about-copy">
      <p>Brightline Coatings Co is a family-owned fabrication studio built on a simple belief: coastal homes and commercial builds deserve hardware that's engineered as carefully as it looks.</p>
      <p>Every handrail, balustrade and gate is measured, fabricated and finished in-house — no shortcuts, no generic stock parts.</p>
    </div>
    <div class="about-side">
      <div class="about-heading-block">
        <div class="eyebrow">Who We Are</div>
        <h2 class="about-title">Crafted with precision<br>installed with pride</h2>
      </div>
      <div class="about-photo" role="img" aria-label="Waterfront home with powder coated balustrades overlooking the bay">
        <div class="stat-badge">
          <div class="stat-value">14+</div>
          <div class="stat-label">Years of craft</div>
        </div>
      </div>
    </div>
  </section>
</div>
</body>
</html>
```